MV Decor

There is a sample provided with the arabic text of the business card. please copy paste the same text and the same Logo (The two triangles) Just try to incorproate the Brown background attached (you are free to change the colors) Id like the colors to be mainly shades of black and red.

```html
<!DOCTYPE html>
<html lang="ar">
<head>
<meta charset="utf-8">
<title>MV Decor — Business Card</title>
<link rel="stylesheet" href="https://fonts.googleapis.com/css2?family=Tajawal:wght@300;500&family=Aref+Ruqaa&family=Roboto:wght@400&display=swap">
<style>
  :root {
    --backdrop: #2b2b2b;
    --card-red: #cc2340;
    --card-red-light: #e0334f;
    --card-red-deep: #b81c37;
    --ink-light: #ffffff;
    --ink-dark: #1f1f1f;
  }
  * { box-sizing: border-box; margin: 0; padding: 0; }
  html, body {
    width: 1125px; height: 1200px; overflow: hidden;
    background: var(--backdrop);
  }
  .canvas { position: relative; width: 1125px; height: 1200px; }
  .card {
    position: absolute; left: 171px; width: 825px; height: 472px;
    box-shadow: 0 4px 10px rgba(0,0,0,.55);
    overflow: hidden; color: var(--ink-light);
  }
  .card--front { top: 106px; }
  .card--back { top: 639px; }
  .card__texture {
    position: absolute; inset: 0;
    background:
      radial-gradient(ellipse at 45% 35%, var(--card-red-light) 0%, transparent 55%),
      radial-gradient(ellipse at 75% 70%, rgba(240,70,95,.45) 0%, transparent 50%),
      linear-gradient(160deg, var(--card-red) 0%, var(--card-red-deep) 100%);
  }
  .brand {
    position: absolute; display: flex; flex-direction: column; align-items: center;
    font-family: "Tajawal", sans-serif; font-weight: 500; color: var(--ink-light);
  }
  .brand__square { background: var(--ink-dark); }
  .card--front .brand { left: 610px; top: 70px; width: 170px; gap: 18px; }
  .card--front .brand__square { width: 64px; height: 64px; }
  .card--front .brand__name { font-size: 34px; letter-spacing: 1px; }
  .card--back .brand { left: 110px; top: 150px; width: 280px; gap: 22px; }
  .card--back .brand__square { width: 90px; height: 90px; }
  .card--back .brand__name { font-size: 46px; letter-spacing: 1px; }

  .credentials {
    position: absolute; right: 60px; top: 312px;
    direction: rtl; list-style: none;
    font-family: "Tajawal", sans-serif; font-weight: 300;
    font-size: 22px; line-height: 27px;
  }
  .person {
    position: absolute; left: 70px; top: 290px; width: 250px;
    direction: rtl; text-align: center;
    font-family: "Aref Ruqaa", serif;
  }
  .person__name { font-size: 24px; line-height: 32px; }
  .person__title { font-size: 17px; line-height: 24px; opacity: .95; }
  .phone {
    position: absolute; left: 60px; top: 400px;
    display: flex; align-items: center; gap: 6px;
    font-family: "Roboto", sans-serif; font-size: 22px;
  }
  .phone svg { width: 20px; height: 20px; fill: var(--ink-light); }

  .services {
    position: absolute; right: 114px; top: 106px;
    direction: rtl; list-style: none;
    font-family: "Tajawal", sans-serif; font-weight: 300;
    font-size: 25px; line-height: 33px;
  }
  .services li { display: flex; align-items: center; gap: 10px; }
  .services li::after {
    content: ""; width: 8px; height: 8px; border-radius: 50%;
    background: var(--ink-dark);
  }
</style>
</head>
<body>
<div class="canvas">

  <section class="card card--front">
    <div class="card__texture" role="img" aria-label="Red background with a soft grid pattern of small squares and circles"></div>
    <div class="brand">
      <span class="brand__square"></span>
      <span class="brand__name">MV DECOR</span>
    </div>
    <ul class="credentials">
      <li>ماجستير هندسة ديكور</li>
      <li>دبلوم عالي فن تشكيلي</li>
      <li>جامعة الرواق (باريس)</li>
      <li>استشارات هندسية-فنية</li>
    </ul>
    <div class="person">
      <p class="person__name">المهندس / محمد سالم الراشد</p>
      <p class="person__title">أستاذ جامعي</p>
    </div>
    <p class="phone">
      <svg viewBox="0 0 24 24" aria-hidden="true"><path d="M6.6 10.8a15.1 15.1 0 0 0 6.6 6.6l2.2-2.2c.3-.3.7-.4 1-.2 1.1.4 2.3.6 3.6.6.6 0 1 .4 1 1V20c0 .6-.4 1-1 1A17 17 0 0 1 3 4c0-.6.4-1 1-1h3.5c.6 0 1 .4 1 1 0 1.3.2 2.5.6 3.6.1.3 0 .7-.2 1z"/></svg>
      <span>30214587 / 60538214</span>
    </p>
  </section>

  <section class="card card--back">
    <div class="card__texture" role="img" aria-label="Red background with a soft grid pattern of small squares and circles"></div>
    <div class="brand">
      <span class="brand__square"></span>
      <span class="brand__name">MV DECOR</span>
    </div>
    <ul class="services">
      <li>ماجستير هندسة ديكور</li>
      <li>دبلوم عالي فن تشكيلي</li>
      <li>جامعة الرواق (باريس)</li>
      <li>استشارات هندسية-فنية</li>
      <li>ماجستير هندسة ديكور</li>
      <li>دبلوم عالي فن تشكيلي</li>
      <li>جامعة الرواق (باريس)</li>
      <li>استشارات هندسية-فنية</li>
    </ul>
  </section>

</div>
</body>
</html>
```